New Email Marketing Design Project

I’d like you to make an email template. I’ll be welcoming and on boarding customers via email. And I’d like the branding to stand out. Keep it professional and simple. But be creative.

Design should look amazing on desktop and mobile phones.

Negative white space is ok.

Use stock images

I’ll like to have a spot for a picture of myself so make sure to include a circle where I can show my face so that email viewers will know who is speaking to them.

Target Market(s)

Practice managers, doctors, medical providers

Font styles to use
Sans Serif

Requirements
Must have
• Our Logo, CTA buttons, Same colors as website.
https://www.tarvoclaimservices.com

```html
<!DOCTYPE html>
<html lang="en">
<head>
<meta charset="utf-8">
<title>Tarvo Claim Services – Welcome</title>
<link href="https://fonts.googleapis.com/css2?family=Montserrat:wght@400;500;700&family=Open+Sans:wght@700&display=swap" rel="stylesheet">
<style>
:root{
  --page:#f4f5f7;
  --navy:#0d2f52;
  --blue:#2f75a0;
  --blue-mid:#3a84b0;
  --sky:#8fb0de;
  --photo-light:#dfe7ec;
  --photo-mid:#b9c8d2;
  --ink:#141414;
  --white:#ffffff;
}
*{box-sizing:border-box;margin:0;padding:0}
html,body{width:1200px;height:1014px;overflow:hidden;background:var(--page)}
body{font-family:"Montserrat",sans-serif}
a{text-decoration:none;color:inherit}
.email{position:absolute;left:220px;top:0;width:760px;height:1014px;overflow:hidden;background:var(--photo-light)}
.hero-photo{position:absolute;inset:0;background:linear-gradient(160deg,#eef2f4 0%,var(--photo-light) 40%,var(--photo-mid) 75%,#8e9ea9 100%)}
.edge-strip{position:absolute;left:0;top:0;width:16px;height:100%;background:#c9cdd1}
.band-blue{position:absolute;left:16px;top:0;width:41px;height:100%;background:rgba(47,117,160,.92)}
.band-navy{position:absolute;left:57px;top:0;width:187px;height:100%;background:rgba(13,47,82,.9)}

.header-tab{position:absolute;left:309px;top:0;width:431px;height:59px;background:var(--white);border-bottom-left-radius:26px;display:flex;align-items:center;padding-left:70px;gap:14px}
.brand-dot{width:26px;height:26px;border:3px solid var(--blue);border-radius:50%}
.brand-name{font-family:"Open Sans",sans-serif;font-weight:700;font-size:17px;color:var(--blue)}

.portrait{position:absolute;left:37px;top:83px;width:290px;height:290px;border-radius:50%;border:7px solid var(--blue);background:radial-gradient(circle at 50% 40%,#e9eef2,#b8c6d1 70%,#8ea3b4)}
.cta-services{position:absolute;left:63px;top:292px;width:271px;height:55px;background:var(--ink);border-radius:0 28px 28px 0;color:var(--white);font-size:22px;letter-spacing:6px;display:flex;align-items:center;padding-left:20px}

.cta-service{position:absolute;left:487px;width:253px;height:44px;background:var(--blue);border-radius:22px 0 0 22px;color:var(--white);font-size:23px;letter-spacing:6px;display:flex;align-items:center;padding-left:24px}
.service-text{position:absolute;left:507px;width:233px;height:66px;background:var(--ink);color:var(--white);font-size:12.5px;line-height:14px;text-align:center;display:flex;align-items:center;justify-content:center;padding:0 6px}

.title{position:absolute;left:63px;top:446px;color:var(--white)}
.title-strong{display:block;font-weight:700;font-size:62px;line-height:72px;text-shadow:2px 2px 3px rgba(0,0,0,.45)}
.title-light{display:block;font-weight:400;font-size:60px;line-height:72px;color:var(--sky);text-shadow:2px 2px 3px rgba(0,0,0,.55)}

.intro{position:absolute;left:16px;top:638px;width:449px;height:82px;background:var(--blue);color:var(--white);font-size:14.5px;line-height:17px;padding:11px 16px 0 65px}

.footer-shape{position:absolute;inset:0}
.contact{position:absolute;left:280px;top:876px;list-style:none;color:var(--white);font-size:9.5px;font-weight:700;line-height:11px}
.contact li{display:flex;align-items:center;gap:8px;height:27px}
.contact svg{flex:none}
.divider{position:absolute;left:490px;top:880px;width:2px;height:98px;background:var(--white)}
.social{position:absolute;left:535px;top:872px;list-style:none;color:var(--white);font-size:16px}
.social li{display:flex;align-items:center;gap:14px;height:39px}
.social-dot{width:14px;height:14px;border-radius:50%;background:var(--white)}
</style>
</head>
<body>
<main class="email">
  <div class="hero-photo" role="img" aria-label="Stock photo of a bright clinic desk with a stethoscope and laptop"></div>
  <div class="edge-strip"></div>
  <div class="band-blue"></div>
  <div class="band-navy"></div>

  <header class="header-tab">
    <span class="brand-dot"></span>
    <a class="brand-name" href="https://www.tarvoclaimservices.com">Tarvo Claim Services</a>
  </header>

  <div class="portrait" role="img" aria-label="Circular portrait photo of the practice owner"></div>
  <a class="cta-services" href="https://www.tarvoclaimservices.com">OUR SERVICES</a>

  <a class="cta-service" style="top:166px" href="https://www.tarvoclaimservices.com">SERVICE 1</a>
  <p class="service-text" style="top:217px">Lorem ipsum dolor sit amet, consectetuer adipiscing elit, sed diam nonummy nibh euismod.</p>
  <a class="cta-service" style="top:361px" href="https://www.tarvoclaimservices.com">SERVICE 2</a>
  <p class="service-text" style="top:412px">Lorem ipsum dolor sit amet, consectetuer adipiscing elit, sed diam nonummy nibh euismod.</p>

  <h1 class="title">
    <span class="title-strong">Tarvo Claim</span>
    <span class="title-light">Services</span>
  </h1>

  <p class="intro">Lorem ipsum dolor sit amet, consectetuer adipiscing elit, sed diam nonummy nibh euismod tincidunt ut laoreet dolore magna aliquam erat volutpat.</p>

  <svg class="footer-shape" width="760" height="1014" viewBox="0 0 760 1014" aria-hidden="true">
    <path d="M96 1014 C120 900 300 860 520 800 C660 760 740 700 740 560 V1014 Z" fill="var(--blue)"/>
    <path d="M80 960 C160 860 330 830 560 810 C690 795 740 720 740 640 C720 760 600 800 420 820 C260 840 150 880 80 960 Z" fill="var(--sky)"/>
    <path d="M110 900 C200 820 320 800 460 800 C330 815 220 840 110 900 Z" fill="var(--blue-mid)"/>
  </svg>

  <ul class="contact">
    <li><svg width="12" height="14" viewBox="0 0 12 14"><path d="M6 0a5 5 0 0 1 5 5c0 4-5 9-5 9S1 9 1 5a5 5 0 0 1 5-5z" fill="#fff"/><circle cx="6" cy="5" r="2" fill="#2f75a0"/></svg><span>210 Larkfield Ave Ste 400,<br>Eastbrook, Minnesota 55990</span></li>
    <li><svg width="12" height="14" viewBox="0 0 12 14"><rect x="2" y="0" width="8" height="14" rx="2" fill="none" stroke="#fff" stroke-width="1.6"/></svg><span>555-018-2274</span></li>
    <li><svg width="12" height="12" viewBox="0 0 12 12"><rect x="0" y="3" width="12" height="9" rx="1" fill="#fff"/><rect x="3" y="0" width="6" height="4" fill="#fff"/></svg><span>555-018-2274</span></li>
    <li><svg width="12" height="10" viewBox="0 0 12 10"><rect width="12" height="10" rx="1" fill="#fff"/><path d="M0 1l6 4 6-4" stroke="#2f75a0" fill="none"/></svg><span>hello@tarvoclaimservices.com</span></li>
  </ul>
  <div class="divider"></div>
  <ul class="social">
    <li><span class="social-dot"></span><span>YourAccount</span></li>
    <li><span class="social-dot"></span><span>@YourAccount</span></li>
    <li><span class="social-dot"></span><span>@YourAccount</span></li>
  </ul>
</main>
</body>
</html>
```